Professional violinist needs business cards

I am trying to attract the following jobs:
-private violin lessons (primarily classical)
-performance gigs (weddings, birthday parties, funerals, etc.)
-collaborations with other artists (studio recordings, performances)

I want to communicate that I have a very high standard of excellence for my work, but I also love people and celebrations.
Values/style words I like are:
love, joy, peace, fun, beauty, authenticity, excellence, warmth, refined/sleek, free spirited. If that's too confusing, just ignore :)

I will attach my favorite business card template that I could find on Canva. The lines are supposed to be like a music staff, which I think is really cool, but I also don't want it to look too busy. I like the simple black and white--I think it looks sharp--but I also am open to other ideas. I also have seen business cards with pictures included that looked great, so I attached an image that could be used as well.

I am also attaching a file that I made of my initials that could be used as a logo, but I'm not sure if it should be included.

Information on the card:
-My name (18 letters total)
-"violinist"
-phone number, email, website

Thank you!

```html
<!DOCTYPE html>
<html lang="en">
<head>
<meta charset="UTF-8">
<title>Lucia Harrowgate – Business Card</title>
<link href="https://fonts.googleapis.com/css2?family=Barlow+Condensed:wght@300;400;600&display=swap" rel="stylesheet">
<style>
  :root {
    --backdrop: #8e9094;
    --card: #050506;
    --ink: #ffffff;
    --staff: rgba(255,255,255,0.85);
  }
  * { box-sizing: border-box; margin: 0; padding: 0; }
  html, body {
    width: 1200px; height: 1200px; overflow: hidden;
    background: var(--backdrop);
    font-family: "Barlow Condensed", "Arial Narrow", sans-serif;
  }
  .card {
    position: absolute; left: 160px;
    width: 880px; height: 503px;
    background: var(--card);
    overflow: hidden;
    box-shadow: 0 14px 30px rgba(0,0,0,0.35);
  }
  .card--front { top: 66px; }
  .card--back { top: 630px; }

  .staff-line {
    position: absolute; height: 1.5px;
    background: var(--staff);
  }

  /* front */
  .wordmark {
    position: absolute; left: 120px; top: 188px;
    padding: 22px 34px;
    background: var(--card);
    color: var(--ink);
    font-weight: 600; font-size: 76px; line-height: 1;
    letter-spacing: 0.02em; text-transform: uppercase;
  }

  /* back */
  .name {
    position: absolute; right: 80px; top: 78px;
    color: var(--ink); font-size: 58px; line-height: 1;
    text-transform: uppercase; letter-spacing: 0.01em;
  }
  .name__first { font-weight: 600; }
  .name__last { font-weight: 300; }
  .role {
    position: absolute; left: 380px; top: 152px;
    color: var(--ink); font-weight: 300; font-size: 26px;
    letter-spacing: 0.55em; text-transform: uppercase;
  }
  .contact {
    position: absolute; left: 380px;
    color: var(--ink); font-weight: 400; font-size: 36px; line-height: 1;
  }
  .contact--phone { top: 212px; }
  .contact--email { top: 278px; }
  .contact--web { top: 344px; }
</style>
</head>
<body>

<section class="card card--front" aria-label="Card front">
  <div class="staff-line" style="left:0;right:0;top:70px"></div>
  <div class="staff-line" style="left:0;right:0;top:135px"></div>
  <div class="staff-line" style="left:0;right:0;top:200px"></div>
  <div class="staff-line" style="left:0;right:0;top:265px"></div>
  <div class="staff-line" style="left:0;right:0;top:330px"></div>
  <div class="staff-line" style="left:0;right:0;top:395px"></div>
  <div class="staff-line" style="left:0;right:0;top:460px"></div>
  <div class="wordmark">Lucia Harrowgate</div>
</section>

<section class="card card--back" aria-label="Card back">
  <h1 class="name"><span class="name__first">Lucia</span> <span class="name__last">Harrowgate</span></h1>
  <p class="role">Violinist</p>
  <div class="staff-line" style="left:0;width:360px;top:168px"></div>

  <p class="contact contact--phone">+00 1234 555 010</p>
  <div class="staff-line" style="left:0;right:0;top:256px"></div>

  <p class="contact contact--email">luciaharrowgate@postmail.com</p>
  <div class="staff-line" style="left:0;right:0;top:322px"></div>

  <p class="contact contact--web">www.luciaharrowgate.com</p>
  <div class="staff-line" style="left:0;right:0;top:388px"></div>

  <div class="staff-line" style="left:0;right:0;top:454px"></div>
</section>

</body>
</html>
```